Modern Business Card for Larkwell 2018

Our company assumes the best about people. We are creating an online community of entrepreneurs and business leaders who struggle with marketing their business online.

This business card should POP! We recently got a new logo and are launching a new website next month, so our business cards should make a statement that feels:
-Fresh
-Smart
-Trustworthy
-Fun

Target Market(s)

small business owners, entrepreneurs

Industry/Entity Type

Digital Marketing

Contact Information for Business Card

Dimensions: 3.5" x 2"

Font styles to use
Sans Serif

Colors
f37122
ffffff

Requirements
Must have
• We need a business card with a modern, bold design. We will use one side of the card as a lead-generation offer, so text on one side will need to fit up to 140 characters. The business card should stick to our core colors (orange, black, and white).
Nice to have
• We think a vertical "portrait" design could be interesting.
Should not have
• Should not look like a traditional business card. The round icon should stand out from a distance.

```html
<!DOCTYPE html>
<html lang="en">
<head>
<meta charset="utf-8">
<title>Larkwell Business Card</title>
<link rel="stylesheet" href="https://fonts.googleapis.com/css2?family=Montserrat:wght@500;700;800;900&family=Oswald:wght@500;600&family=Architects+Daughter&display=swap">
<style>
  :root {
    --orange: #f37122;
    --white: #ffffff;
    --ink: #1d1d1d;
    --grey: #3a3a3a;
    --stage: #e9e6e1;
    --silver-light: #f4f4f4;
    --silver-dark: #c9c9c9;
  }
  * { box-sizing: border-box; margin: 0; padding: 0; }
  html, body { width: 1200px; height: 911px; overflow: hidden; }
  body {
    background: var(--stage);
    position: relative;
    font-family: "Montserrat", sans-serif;
  }

  /* Front: landscape card */
  .card-front {
    position: absolute;
    left: 60px; top: 284px;
    width: 600px; height: 343px;
    background: var(--white);
    box-shadow: 0 6px 18px rgba(0,0,0,0.18);
    overflow: hidden;
  }
  .front-mark {
    position: absolute;
    right: 30px; top: 36px;
    display: flex; align-items: center; gap: 14px;
  }
  .front-mark .dot {
    flex: none;
    width: 160px; height: 160px; border-radius: 50%;
    background: var(--orange);
  }
  .front-mark .brand {
    font-weight: 800; font-size: 28px; letter-spacing: 2px;
    color: var(--orange);
    white-space: nowrap;
  }
  .contact {
    position: absolute;
    left: 34px; bottom: 30px;
    font-family: "Oswald", sans-serif;
    line-height: 1.1;
  }
  .contact .name { font-weight: 600; font-size: 30px; color: var(--ink); letter-spacing: 0.5px; }
  .contact .role { font-weight: 600; font-size: 25px; color: var(--orange); letter-spacing: 0.5px; }
  .contact .email { font-weight: 500; font-size: 23px; color: var(--grey); letter-spacing: 0.5px; }

  /* Back: portrait lead-generation card */
  .card-back {
    position: absolute;
    left: 780px; top: 155px;
    width: 343px; height: 600px;
    background: var(--orange);
    color: var(--white);
    box-shadow: 0 6px 18px rgba(0,0,0,0.18);
    padding: 34px 26px 0;
    text-align: center;
    overflow: hidden;
  }
  .back-brand { display: flex; flex-direction: column; align-items: center; gap: 8px; }
  .back-brand .dot { width: 46px; height: 46px; border-radius: 50%; background: var(--white); }
  .back-brand .brand { font-weight: 900; font-size: 46px; letter-spacing: 2px; line-height: 1; }
  .tagline {
    font-family: "Architects Daughter", sans-serif;
    font-size: 12px; letter-spacing: 0.5px; text-transform: uppercase;
    white-space: nowrap;
    margin-top: 8px;
  }
  .promise {
    margin-top: 16px;
    font-weight: 900; font-size: 19px; line-height: 1.15; letter-spacing: 0.5px;
    text-transform: uppercase;
  }
  .write-in {
    margin: 18px auto 0;
    width: 290px; height: 190px;
    border-radius: 14px;
    background: linear-gradient(135deg, var(--silver-light), var(--silver-dark) 55%, var(--silver-light));
    padding: 26px 20px 0;
  }
  .write-in .line { border-bottom: 1px dotted #444; height: 28px; }
  .offer {
    margin-top: 22px;
    font-weight: 500; font-size: 15px; line-height: 1.3; letter-spacing: 0.5px;
    text-transform: uppercase;
  }
  .offer strong { font-weight: 800; }
  .offer-link {
    display: inline-block;
    margin-top: 12px;
    padding: 6px 22px;
    border-radius: 20px;
    background: #111;
    color: var(--orange);
    font-weight: 800; font-size: 16px;
  }
</style>
</head>
<body>
  <section class="card-front">
    <div class="front-mark">
      <span class="dot"></span>
      <span class="brand">LARKWELL</span>
    </div>
    <div class="contact">
      <p class="name">DANA WHITFIELD</p>
      <p class="role">STORY MARKETING COACH</p>
      <p class="email">DANA@LARKWELLNOW.COM</p>
    </div>
  </section>

  <section class="card-back">
    <div class="back-brand">
      <span class="dot"></span>
      <span class="brand">LARKWELL</span>
    </div>
    <p class="tagline">Tell stories that inspire action</p>
    <p class="promise">Reach more people.<br>Make more money.<br>Create more impact.</p>
    <div class="write-in">
      <div class="line"></div>
      <div class="line"></div>
      <div class="line"></div>
      <div class="line"></div>
      <div class="line"></div>
    </div>
    <p class="offer">Get your free <strong>Larkwell</strong><br>starter package and our<br>marketing guide today at</p>
    <span class="offer-link">larkwellnow.com/start</span>
  </section>
</body>
</html>
```